RWT Fittings Ltd Business Cards

We need a business card with our business logo. We provide window and door installations on high-rises in west coast British Colombia, Canada.

I would like my business information and details on one side of the card, and the other side the company name with logo

Target Market(s)

General Contractors

Industry/Entity Type

Construction

Contact Information for Business Card

one side i want my company name and logo in the dark theme logo that i provided

Requirements
Must have
• Marco Peltieri, 16045518293, RWTFittings@mailbox-demo.com, 1407-5194 Linden Row Burnaby BC, V5H 2K9, Owner & Manager

```html
<!DOCTYPE html>
<html lang="en">
<head>
<meta charset="utf-8">
<title>RWT Fittings Ltd – Business Cards</title>
<link rel="stylesheet" href="https://fonts.googleapis.com/css2?family=Montserrat:wght@400;500;700&display=swap">
<style>
  :root {
    --stage: #e6e6e6;
    --stage-edge: #cfcfcf;
    --dark-card: #3f3b38;
    --dark-card-deep: #2e2b29;
    --brand-blue: #3ba3d6;
    --brand-light-blue: #5cc6ea;
    --brand-grey: #9a9a9a;
    --text-grey: #6b6b6b;
    --white-card: #f4f4f4;
    --divider: #9d9d9d;
  }
  * { box-sizing: border-box; margin: 0; padding: 0; }
  html, body {
    width: 1200px; height: 1200px; overflow: hidden;
  }
  body {
    background: radial-gradient(circle at 30% 30%, var(--stage) 0%, var(--stage-edge) 100%);
    font-family: "Montserrat", sans-serif;
    position: relative;
  }
  .card {
    position: absolute;
    left: 180px;
    width: 840px;
    height: 480px;
    border-radius: 28px;
    box-shadow: 0 14px 30px rgba(0,0,0,0.22);
    overflow: hidden;
  }
  /* Front side */
  .card--front { top: 70px; background: var(--dark-card); }
  .front-photo {
    position: absolute; inset: 0;
    background: linear-gradient(135deg, #4a4643 0%, var(--dark-card) 50%, var(--dark-card-deep) 100%);
  }
  .front-brand {
    position: absolute; inset: 0;
    display: flex; align-items: center; justify-content: center; gap: 22px;
  }
  .brand-square {
    width: 46px; height: 46px; background: var(--brand-light-blue);
  }
  .brand-name {
    font-weight: 700; font-size: 64px; letter-spacing: 1px;
    color: var(--brand-light-blue);
  }
  /* Back side */
  .card--back {
    top: 640px; background: linear-gradient(120deg, #fafafa 0%, var(--white-card) 60%, #e9e9e9 100%);
  }
  .back-brand {
    position: absolute; left: 70px; top: 0; height: 100%; width: 330px;
    display: flex; align-items: center; gap: 14px;
  }
  .back-brand .brand-square { width: 28px; height: 28px; background: var(--brand-blue); }
  .back-brand .brand-name { font-size: 34px; color: var(--brand-blue); letter-spacing: 0.5px; }
  .back-divider {
    position: absolute; left: 420px; top: 120px; width: 2px; height: 240px;
    background: var(--divider);
  }
  .contact {
    position: absolute; left: 455px; top: 112px; width: 360px;
    color: var(--text-grey);
  }
  .contact__name { font-weight: 700; font-size: 32px; color: var(--brand-blue); line-height: 1.1; }
  .contact__role { font-size: 17px; margin-top: 6px; letter-spacing: 0.3px; }
  .contact__address { font-size: 16px; margin-top: 18px; line-height: 1.4; }
  .contact__list { list-style: none; margin-top: 16px; font-size: 15px; }
  .contact__list li { display: flex; align-items: center; gap: 10px; line-height: 1.75; }
  .contact__list svg { width: 16px; height: 16px; fill: var(--brand-blue); flex: none; }
</style>
</head>
<body>

<section class="card card--front">
  <div class="front-photo" role="img" aria-label="Softly blurred dark interior photograph behind the company name"></div>
  <div class="front-brand">
    <span class="brand-square"></span>
    <span class="brand-name">RWT Fittings Ltd</span>
  </div>
</section>

<section class="card card--back">
  <div class="back-brand">
    <span class="brand-square"></span>
    <span class="brand-name">RWT Fittings Ltd</span>
  </div>
  <div class="back-divider"></div>
  <div class="contact">
    <p class="contact__name">Marco Peltieri</p>
    <p class="contact__role">Owner &amp; Manager</p>
    <p class="contact__address">1407-5194 Linden Row<br>Burnaby BC, V5H 2K9</p>
    <ul class="contact__list">
      <li>
        <svg viewBox="0 0 24 24" aria-hidden="true"><path d="M6.6 10.8a15.1 15.1 0 0 0 6.6 6.6l2.2-2.2a1 1 0 0 1 1-.25 11.4 11.4 0 0 0 3.6.57 1 1 0 0 1 1 1V20a1 1 0 0 1-1 1A17 17 0 0 1 3 4a1 1 0 0 1 1-1h3.5a1 1 0 0 1 1 1c0 1.25.2 2.45.57 3.57a1 1 0 0 1-.25 1z"/></svg>
        (604)-551-8293
      </li>
      <li>
        <svg viewBox="0 0 24 24" aria-hidden="true"><path d="M2 5h20v14H2z" fill="none"/><path d="M2 5h20v14H2V5zm2 2v.4l8 5 8-5V7H4z"/></svg>
        RWTFittings@mailbox-demo.com
      </li>
      <li>
        <svg viewBox="0 0 24 24" aria-hidden="true"><path d="M12 2a10 10 0 1 0 0 20 10 10 0 0 0 0-20zm6.9 6h-3a15 15 0 0 0-1.3-4A8 8 0 0 1 18.9 8zM12 4c.8 1.2 1.5 2.5 1.9 4h-3.8c.4-1.5 1.1-2.8 1.9-4zM4.3 14a8 8 0 0 1 0-4h3.4a16 16 0 0 0 0 4H4.3zm.8 2h3a15 15 0 0 0 1.3 4A8 8 0 0 1 5.1 16zm3-8h-3a8 8 0 0 1 4.3-4A15 15 0 0 0 8.1 8zM12 20c-.8-1.2-1.5-2.5-1.9-4h3.8c-.4 1.5-1.1 2.8-1.9 4zm2.3-6H9.7a14 14 0 0 1 0-4h4.6a14 14 0 0 1 0 4zm.3 6a15 15 0 0 0 1.3-4h3a8 8 0 0 1-4.3 4zm1.7-6a16 16 0 0 0 0-4h3.4a8 8 0 0 1 0 4h-3.4z"/></svg>
        www.rwtfittings-demo.com
      </li>
    </ul>
  </div>
</section>

</body>
</html>
```